Business Card Design

WE are looking for a premium quality Business Cards for a Law Firm . Copies of our current business card is attached.

Contact Information for Business Card

xyz

```html
<!DOCTYPE html>
<html lang="en">
<head>
<meta charset="utf-8">
<title>Harrowgate Lawyers – Business Card</title>
<link href="https://fonts.googleapis.com/css2?family=Cinzel:wght@600;700&family=Arimo:wght@400;700&display=swap" rel="stylesheet">
<style>
  :root{
    --gold:#c59d5f;
    --gold-text:#b8955a;
    --green:#1d3a2b;
    --ink:#1b1b1b;
    --white:#ffffff;
    --paper:#f7f7f5;
    --backdrop:#2b2b2b;
    --rule:#b5b5b5;
  }
  *{box-sizing:border-box;margin:0;padding:0}
  html,body{width:1200px;height:768px;overflow:hidden}
  body{background:var(--backdrop);font-family:"Arimo",Arial,sans-serif;display:flex;align-items:center;justify-content:center;gap:40px}
  .card{width:540px;height:310px;border-radius:18px;position:relative;overflow:hidden;background:var(--gold)}

  /* back */
  .firm{position:absolute;top:44px;left:0;right:0;text-align:center;color:var(--white)}
  .firm-circle{width:66px;height:66px;border:3px solid var(--white);border-radius:50%;margin:0 auto 14px}
  .firm-name{font-family:"Cinzel",serif;font-weight:600;font-size:28px;letter-spacing:2px}
  .offices{position:absolute;left:22px;right:22px;bottom:34px;display:flex;color:var(--white)}
  .office{flex:1;text-align:center;font-size:11px;line-height:1.35;padding:12px 6px 0}
  .office+.office{border-left:1.5px solid rgba(255,255,255,.85)}
  .office h3{font-size:14px;font-weight:700;margin-bottom:3px}
  .office b{font-weight:700}

  /* front */
  .card-front .oval{position:absolute;left:48px;top:-30px;width:480px;height:370px;border-radius:50%;background:var(--paper)}
  .profile{position:absolute;left:48px;width:480px;top:26px;text-align:center}
  .mark{display:flex;align-items:center;justify-content:center;gap:8px;margin-bottom:10px}
  .mark-circle{width:58px;height:58px;border:3px solid var(--gold);border-radius:50%}
  .mark-name{font-family:"Cinzel",serif;font-weight:700;font-size:13px;color:var(--green);letter-spacing:1px}
  .person{font-family:"Cinzel",serif;font-weight:700;font-size:26px;color:var(--green);letter-spacing:1px}
  .role{font-size:14px;color:var(--gold-text);line-height:1.25;margin-top:2px}
  .address{font-size:14px;color:var(--ink);line-height:1.3;margin-top:8px;position:relative}
  .address .rule{display:block;height:1px;background:var(--rule);width:70px;position:absolute;top:29px}
  .address .rule.l{left:42px}.address .rule.r{right:42px}
  .contacts{text-align:left;width:max-content;margin:10px auto 0;font-size:14px;color:var(--ink);line-height:1.4}
  .contacts li{list-style:none;display:flex;align-items:center;gap:7px}
  .contacts svg{width:11px;height:11px;fill:var(--green);flex:none}
  .gap{margin-left:14px}
</style>
</head>
<body>
  <section class="card card-back">
    <div class="firm">
      <div class="firm-circle"></div>
      <div class="firm-name">HARROWGATE LAWYERS</div>
    </div>
    <div class="offices">
      <div class="office">
        <h3>Melbourne</h3>
        Level 12, 240 Flinders Lane<br>Melbourne, VIC 3000<br><b>Phone :</b> +61 03 9000 1482
      </div>
      <div class="office">
        <h3>Sydney</h3>
        Level 15, 60 Park Street<br>Sydney, NSW 2000<br><b>Phone :</b> +61 02 9000 3356
      </div>
      <div class="office">
        <h3>Perth</h3>
        Level 9, Swan Tower<br>88 Riverside Terrace<br>Perth, WA 6000<br><b>Phone :</b> +61 08 6000 2917
      </div>
    </div>
  </section>

  <section class="card card-front">
    <div class="oval"></div>
    <div class="profile">
      <div class="mark"><span class="mark-circle"></span><span class="mark-name">HARROWGATE LAWYERS</span></div>
      <div class="person">DANIEL MARSH</div>
      <div class="role">Director &amp; Principal Solicitor<br>MBA, Juris Doctor</div>
      <div class="address">
        Level 3, Harrowgate House, 72 Ridge Terrace<br>Spring Hill, QLD 4000
        <span class="rule l"></span><span class="rule r"></span>
      </div>
      <ul class="contacts">
        <li><svg viewBox="0 0 24 24"><path d="M6.6 10.8a15 15 0 0 0 6.6 6.6l2.2-2.2a1 1 0 0 1 1-.25 11.4 11.4 0 0 0 3.6.57 1 1 0 0 1 1 1V20a1 1 0 0 1-1 1A17 17 0 0 1 3 4a1 1 0 0 1 1-1h3.5a1 1 0 0 1 1 1c0 1.25.2 2.45.57 3.57a1 1 0 0 1-.25 1z"/></svg>+61 7 3000 4418
          <svg class="gap" viewBox="0 0 24 24"><path d="M7 1h10a2 2 0 0 1 2 2v18a2 2 0 0 1-2 2H7a2 2 0 0 1-2-2V3a2 2 0 0 1 2-2zm0 3v15h10V4z"/></svg>+61 0400 000 327</li>
        <li><svg viewBox="0 0 24 24"><path d="M2 5h20v14H2zm2 2v.5l8 5 8-5V7l-8 5z"/></svg>daniel@harrowgatelawyers.com.au</li>
        <li><svg viewBox="0 0 24 24"><circle cx="12" cy="12" r="10"/></svg>www.harrowgatelawyers.com.au</li>
      </ul>
    </div>
  </section>
</body>
</html>
```